Calvanto Group Real Estate Company business cards

New business card design, we are generally happy with the basic layout of the existing front of business card, (feel free to change) but require a head shot photo on the back side.

http://www.calvanto.com.au/

Attached logos, and existing business card

------------------------------

Target Market(s)

Real estate

Industry/Entity Type

Real Estate

Contact Information for Business Card

Standard size double sided

Font styles to use
Other font styles liked:
• Futura

Requirements
Must have
• Photo head shot on the back side
Nice to have
• yes
Should not have
• No

```html
<!DOCTYPE html>
<html lang="en">
<head>
<meta charset="utf-8">
<title>Calvanto Group – Business Cards</title>
<link href="https://fonts.googleapis.com/css2?family=Open+Sans:wght@400;600;700&display=swap" rel="stylesheet">
<style>
  :root {
    --backdrop: #ecebe8;
    --kraft: #c6a26d;
    --kraft-light: #cdaa76;
    --ink: #161616;
    --suit-navy: #27344f;
    --suit-shade: #3c4a66;
    --card-shadow: rgba(0, 0, 0, 0.25);
  }
  * { margin: 0; padding: 0; box-sizing: border-box; }
  html, body {
    width: 1200px; height: 900px; overflow: hidden;
    background: var(--backdrop);
    font-family: "Open Sans", sans-serif;
    color: var(--ink);
  }
  .canvas { position: relative; width: 1200px; height: 900px; }
  .card {
    position: absolute;
    background: repeating-linear-gradient(90deg, var(--kraft) 0 3px, var(--kraft-light) 3px 5px);
    box-shadow: 0 6px 18px var(--card-shadow);
    overflow: hidden;
  }
  .card-front { left: 78px; top: 35px; width: 587px; height: 363px; }
  .card-back { left: 388px; top: 505px; width: 566px; height: 352px; }

  .headshot {
    position: absolute; left: 0; top: 0; width: 264px; height: 100%;
    background: linear-gradient(180deg, var(--kraft) 0%, var(--suit-shade) 40%, var(--suit-navy) 100%);
  }
  .front-details { position: absolute; left: 284px; top: 0; right: 20px; height: 100%; white-space: nowrap; }
  .front-details > * { position: absolute; left: 0; }
  .brand-name { font-weight: 600; line-height: 1; letter-spacing: 0.3px; white-space: nowrap; }
  .front-details .brand-name { top: 62px; font-size: 31px; }
  .person-name { top: 138px; font-size: 20px; font-weight: 700; line-height: 1.2; }
  .person-role { top: 165px; font-size: 15px; line-height: 1.2; }
  .company-name { top: 202px; font-size: 18px; font-weight: 700; line-height: 1.2; }
  .company-abn { top: 228px; font-size: 15px; line-height: 1.2; }
  .company-abn strong { font-weight: 700; }
  .contact-list { top: 270px; list-style: none; }
  .contact-list li { display: flex; align-items: center; height: 25px; font-size: 15px; }
  .contact-list svg { width: 12px; height: 12px; margin-right: 14px; fill: var(--ink); }

  .back-brand { position: absolute; left: 0; right: 0; top: 180px; text-align: center; font-size: 46px; }
  .services { position: absolute; left: 0; right: 0; top: 266px; text-align: center; font-size: 18px; font-weight: 600; line-height: 1.2; }
  .tagline-row {
    position: absolute; left: 0; right: 0; top: 305px;
    display: flex; align-items: center; gap: 18px;
  }
  .tagline-row .rule { flex: 1; height: 1px; background: var(--ink); }
  .tagline { font-size: 17px; font-weight: 600; white-space: nowrap; }
</style>
</head>
<body>
<main class="canvas">
  <section class="card card-front">
    <div class="headshot" role="img" aria-label="Head-and-shoulders portrait of the director in a navy suit and blue tie"></div>
    <div class="front-details">
      <div class="brand-name">Calvanto Group</div>
      <div class="person-name">Daniel Tran</div>
      <div class="person-role">Director</div>
      <div class="company-name">Calvanto Group</div>
      <div class="company-abn"><strong>ABN:</strong> 12 345 678 901</div>
      <ul class="contact-list">
        <li><svg viewBox="0 0 24 24"><path d="M6.6 10.8a15 15 0 0 0 6.6 6.6l2.2-2.2c.3-.3.7-.4 1-.2 1.1.4 2.3.6 3.6.6.6 0 1 .4 1 1V20c0 .6-.4 1-1 1A17 17 0 0 1 3 4c0-.6.4-1 1-1h3.5c.6 0 1 .4 1 1 0 1.3.2 2.5.6 3.6.1.3 0 .7-.2 1z"/></svg>0412 555 018</li>
        <li><svg viewBox="0 0 24 24"><path d="M2 5h20v14H2z M2 5l10 8 10-8" fill="none" stroke="#161616" stroke-width="2.4"/><path d="M2 5h20l-10 8z"/></svg>daniel.tran@calvanto.com.au</li>
        <li><svg viewBox="0 0 24 24"><circle cx="12" cy="12" r="10"/><path d="M2 12h20M12 2c3 3 3 17 0 20M12 2c-3 3-3 17 0 20" fill="none" stroke="#c6a26d" stroke-width="1.5"/></svg>www.calvanto.com.au</li>
      </ul>
    </div>
  </section>

  <section class="card card-back">
    <div class="brand-name back-brand">Calvanto Group</div>
    <div class="services">Buy&nbsp; | &nbsp;Sell&nbsp; | &nbsp;Rent</div>
    <div class="tagline-row">
      <span class="rule"></span>
      <span class="tagline">let us show you property</span>
      <span class="rule"></span>
    </div>
  </section>
</main>
</body>
</html>
```